Live Webcasting Host Wants Template/Theme to Jumpstare Ecommerce Site

Please,Please, Please READ ALL OF THE DESCRIPTION. Thank you.

I need a template for a look for my developer to work with in designing an ecommerce site where clients pay a monthly fee for streaming services and video on demand.

I'll need 2 pages designed:
1) public page
2) client log in landing page.

Please use a CMS (WP preferred) as this will allow is for further content to be added after delivery. Please include the pricing text in boxes in slides (pdf) to help fill out you design for the home page.

The attached slides are to give you a general layout of how I envision the pages. Yes I would like the Client page to be tabbed from the side like in the attached slide.

I've attached company logos for use along with the accompanying .psd and .ai files in the zip. Use the colors in logo in site design.

Thank you for your time.
Updates

Please, no designs. This is for a CMS for webpage design like WordPress or Joomla. Thanks. Added Friday, January 13, 2017

Target Market(s)

Churches, Organizations, Civic Organizations, Government Agencies (State, Local) -BUT don't let this deter your creativity. Decision makers/influencers will be video production and/or IT personnel.

Industry/Entity Type

It Company

Font styles to use
Sans Serif

Colors
f5f5f5
e8e8e8
333333
fece3e
cbcbcb
33a6d7
000000

Requirements
Must have
• Responsive Design
Nice to have
• One Page Design
Should not have
• SHOULD NOT HAVE White overall background but use white in other ways if you like.

```html
<!DOCTYPE html>
<html lang="en">
<head>
<meta charset="utf-8">
<title>Veloa – Pricing</title>
<link rel="stylesheet" href="https://fonts.googleapis.com/css2?family=Noto+Sans:wght@400;700&family=Oswald:wght@400;500&family=Jost:wght@400;500&display=swap">
<style>
  :root {
    --orange: #f79b22;
    --orange-dark: #d9821a;
    --orange-deep: #e18a1c;
    --blue: #33a6d7;
    --blue-dark: #2487b3;
    --charcoal: #333333;
    --charcoal-dark: #1a1a1a;
    --ink: #333333;
    --text: #444444;
    --white: #ffffff;
    --footer-bg: #ffffff;
    --social: #9a9a9a;
    --bg-top: #dfeee2;
    --bg-mid: #b7d6d6;
    --bg-bottom: #8fa9b8;
  }
  * { box-sizing: border-box; margin: 0; padding: 0; }
  html, body { width: 1200px; height: 695px; overflow: hidden; }
  body { font-family: "Noto Sans", sans-serif; color: var(--ink); background: var(--white); }

  .page { position: relative; width: 1200px; height: 695px; overflow: hidden; }

  .site-header {
    position: absolute; left: 0; top: 0; width: 1200px; height: 97px;
    background: var(--white); box-shadow: 0 2px 6px rgba(0,0,0,.08); z-index: 2;
  }
  .brand {
    position: absolute; left: 74px; top: 26px;
    display: flex; align-items: center; gap: 10px;
    font-family: "Noto Sans", sans-serif; font-weight: 700; font-size: 38px;
    color: var(--ink); letter-spacing: -1px; line-height: 1;
  }
  .brand-dot { width: 16px; height: 16px; border-radius: 50%; background: var(--orange); }

  .main-nav { position: absolute; left: 369px; top: 38px; display: flex; gap: 31px; }
  .main-nav a {
    font-weight: 700; font-size: 15.5px; color: var(--ink); text-decoration: none; text-transform: uppercase;
  }
  .login-button {
    position: absolute; left: 1040px; top: 29px; width: 85px; height: 35px;
    background: var(--orange); color: var(--white); font-weight: 700; font-size: 14px;
    display: flex; align-items: center; justify-content: center; border-radius: 2px; text-decoration: none;
  }

  .hero-backdrop {
    position: absolute; left: 0; top: 97px; width: 1200px; height: 543px;
    background:
      radial-gradient(ellipse 420px 160px at 480px 40px, rgba(240,248,225,.85), transparent 70%),
      radial-gradient(ellipse 600px 240px at 900px 420px, rgba(150,180,200,.5), transparent 70%),
      linear-gradient(180deg, var(--bg-top) 0%, var(--bg-mid) 50%, var(--bg-bottom) 100%);
  }

  .plan {
    position: absolute; top: 171px; width: 332px; height: 396px;
    background: var(--white); box-shadow: 0 14px 18px -8px rgba(40,60,70,.35);
  }
  .plan--small { left: 73px; }
  .plan--medium { left: 434px; }
  .plan--large { left: 793px; }

  .plan-head { position: relative; height: 140px; color: var(--white); text-align: center; }
  .plan-head svg { position: absolute; left: 0; top: 0; }
  .plan-name {
    position: relative; padding-top: 16px; font-family: "Jost", sans-serif; font-size: 21px; font-weight: 400;
  }
  .plan-price {
    position: relative; margin-top: 4px; font-family: "Oswald", sans-serif; font-weight: 400;
    display: flex; justify-content: center; align-items: flex-start; line-height: 1;
  }
  .plan-price .currency { font-size: 18px; margin-top: 6px; margin-right: 4px; }
  .plan-price .amount { font-size: 62px; letter-spacing: -1px; }
  .plan-price .period { font-size: 17px; align-self: flex-end; margin-bottom: 3px; margin-left: 2px; }

  .plan-body { position: relative; padding: 0 20px 0 92px; }
  .plan-icon { position: absolute; left: 28px; top: 12px; }
  .plan-hours { font-size: 26px; font-weight: 700; line-height: 1; padding-top: 17px; color: var(--ink); }
  .plan-hours-label { font-size: 17px; font-weight: 700; line-height: 1.2; }
  .plan-example { font-size: 15px; line-height: 1.3; color: var(--text); margin-top: 2px; }
  .plan-storage { font-size: 15px; font-weight: 700; line-height: 1.3; color: #555; margin-top: 16px; }

  .buy-button {
    position: absolute; left: 93px; top: 319px; width: 165px; height: 48px;
    display: flex; background: var(--orange); border-radius: 3px; box-shadow: 0 3px 0 var(--orange-dark);
    color: var(--white); text-decoration: none; font-weight: 700; font-size: 16px; overflow: hidden;
  }
  .buy-button .label { flex: 1; display: flex; align-items: center; justify-content: center; }
  .buy-button .arrow { width: 40px; background: var(--orange-deep); display: flex; align-items: center; justify-content: center; }

  .site-footer {
    position: absolute; left: 0; top: 640px; width: 1200px; height: 55px; background: var(--footer-bg);
  }
  .legal { position: absolute; left: 79px; top: 17px; font-size: 14.5px; color: var(--text); }
  .legal .sep { margin: 0 8px; }
  .social { position: absolute; left: 1048px; top: 14px; display: flex; gap: 3px; }
  .social span { width: 25px; height: 25px; background: var(--social); display: block; }
</style>
</head>
<body>
<div class="page">
  <header class="site-header">
    <div class="brand"><span>Veloa</span><span class="brand-dot"></span></div>
    <nav class="main-nav">
      <a href="#">Features</a><a href="#">Pricing</a><a href="#">About Us</a><a href="#">Webcasting 101</a><a href="#">Contact</a>
    </nav>
    <a class="login-button" href="#">LOG IN</a>
  </header>

  <div class="hero-backdrop" role="img" aria-label="Soft blurred bokeh light background in pale green and teal tones"></div>

  <article class="plan plan--small">
    <div class="plan-head">
      <svg width="332" height="140" viewBox="0 0 332 140" aria-hidden="true">
        <polygon points="0,0 332,0 332,136 166,140 0,136" fill="#d9821a"/>
        <polygon points="0,0 332,0 332,128 166,132 0,128" fill="#f79b22"/>
      </svg>
      <div class="plan-name">Small</div>
      <div class="plan-price"><span class="currency">$</span><span class="amount">49</span><span class="period">/m</span></div>
    </div>
    <div class="plan-body">
      <svg class="plan-icon" width="46" height="46" viewBox="0 0 46 46" aria-hidden="true" fill="none" stroke="#333" stroke-width="2">
        <rect x="2" y="10" width="40" height="30" rx="2"/><polygon points="16,18 16,32 28,25" fill="#333"/><line x1="2" y1="44" x2="40" y2="44"/><circle cx="37" cy="9" r="8" fill="#fff"/><polyline points="37,5 37,9 40,11"/>
      </svg>
      <div class="plan-hours">400</div>
      <div class="plan-hours-label">Viewer Hours</div>
      <div class="plan-example">(50 Viewers watching 2 hrs- 4 times per month)</div>
      <div class="plan-storage">100 GB/month of video Storage</div>
    </div>
    <a class="buy-button" href="#"><span class="label">Buy Package</span><span class="arrow"><svg width="20" height="16" viewBox="0 0 20 16" aria-hidden="true"><path d="M12 1 L19 7 L12 13 V9 C7 9 3 10 1 14 C1 8 5 5 12 5 Z" fill="#fff"/></svg></span></a>
  </article>

  <article class="plan plan--medium">
    <div class="plan-head">
      <svg width="332" height="140" viewBox="0 0 332 140" aria-hidden="true">
        <polygon points="0,0 332,0 332,136 166,140 0,136" fill="#2487b3"/>
        <polygon points="0,0 332,0 332,128 166,132 0,128" fill="#33a6d7"/>
      </svg>
      <div class="plan-name">Medium</div>
      <div class="plan-price"><span class="currency">$</span><span class="amount">399</span><span class="period">/m</span></div>
    </div>
    <div class="plan-body">
      <svg class="plan-icon" width="46" height="46" viewBox="0 0 46 46" aria-hidden="true" fill="none" stroke="#333" stroke-width="2">
        <rect x="2" y="10" width="40" height="30" rx="2"/><polygon points="16,18 16,32 28,25" fill="#333"/><line x1="2" y1="44" x2="40" y2="44"/><circle cx="37" cy="9" r="8" fill="#fff"/><polyline points="37,5 37,9 40,11"/>
      </svg>
      <div class="plan-hours">4000</div>
      <div class="plan-hours-label">Viewer Hours</div>
      <div class="plan-example">(500 Viewers watching 2 hrs- 4 times per month)</div>
      <div class="plan-storage">500 GB/month of video Storage</div>
    </div>
    <a class="buy-button" href="#"><span class="label">Buy Package</span><span class="arrow"><svg width="20" height="16" viewBox="0 0 20 16" aria-hidden="true"><path d="M12 1 L19 7 L12 13 V9 C7 9 3 10 1 14 C1 8 5 5 12 5 Z" fill="#fff"/></svg></span></a>
  </article>

  <article class="plan plan--large">
    <div class="plan-head">
      <svg width="332" height="140" viewBox="0 0 332 140" aria-hidden="true">
        <polygon points="0,0 332,0 332,136 166,140 0,136" fill="#1a1a1a"/>
        <polygon points="0,0 332,0 332,128 166,132 0,128" fill="#333333"/>
      </svg>
      <div class="plan-name">Latge</div>
      <div class="plan-price"><span class="currency">$</span><span class="amount">999</span><span class="period">/m</span></div>
    </div>
    <div class="plan-body">
      <svg class="plan-icon" width="46" height="46" viewBox="0 0 46 46" aria-hidden="true" fill="none" stroke="#333" stroke-width="2">
        <rect x="2" y="10" width="40" height="30" rx="2"/><polygon points="16,18 16,32 28,25" fill="#333"/><line x1="2" y1="44" x2="40" y2="44"/><circle cx="37" cy="9" r="8" fill="#fff"/><polyline points="37,5 37,9 40,11"/>
      </svg>
      <div class="plan-hours">16000</div>
      <div class="plan-hours-label">Viewer Hours</div>
      <div class="plan-example">(2000 Viewers watching 2 hrs- 4 times per month)</div>
      <div class="plan-storage">2000 GB/month of video Storage</div>
    </div>
    <a class="buy-button" href="#"><span class="label">Buy Package</span><span class="arrow"><svg width="20" height="16" viewBox="0 0 20 16" aria-hidden="true"><path d="M12 1 L19 7 L12 13 V9 C7 9 3 10 1 14 C1 8 5 5 12 5 Z" fill="#fff"/></svg></span></a>
  </article>

  <footer class="site-footer">
    <p class="legal">© 2017 Veloa Streaming. All rights reserved<span class="sep">|</span>Privacy Policy<span class="sep">|</span>Terms of Use</p>
    <div class="social" aria-label="Social links"><span></span><span></span><span></span></div>
  </footer>
</div>
</body>
</html>
```